website design + images

We need a very appealing website design, layout and images for a sales analytics and sales productivity services company based in San Ramon, California. We need a good design for the home page and a template for all other pages (total 2 designs), and images for all inner pages (center column/banner images, and right hand top corner small images). There are about 18 inner pages.
Updates

Our existing website is www.brightvale.com
Our corporate colours are the ones that are there on the website. The logo is also shown. We will be changing the tagline to "accelerating revenue" or equivalent of that.

Please use the document "website for brightvale - template v2.doc" that I just uploaded for any reference to the content, navigation and wireframes. A few more clarifications are provided mainly for the link "Solutions".

Rajesh Kothuri

Hi,
We just uploaded ver 4 of the website template. There is more elaboration provided around the sublinks / sections for Solutions. Pls review and do get back if you need any clarifications.

Rgds
Rajesh Kothuri

Hi all,
We have so far received a few good designs. The designs are more or less on the right track. I would like to urge all of you to use the content and navigation provided in the document attached to our brief "website for brightvale - template v4.doc".  Please DO NOT use the content in our existing website www.brightvale.com . That is very old. We mentioned it only for reference to colour theme and broad details.

We have totally 13 sections in Solutions pages. They may be designed as a tree of links - first level sublinks - second level sublinks or links - first level sublinks and the remaining as sections within the first level sublinks pages. The page design would remain the same for all inner pages except careers. But after finalizing the design for the inner page, we will need images for the different inner pages.

Rgds
Rajesh Kothuri

Hi,
Thank you all for participation and very good designs. We are quite happy with what we have seen. We have now shortlisted about 4 vendors and sending invididual feedback to them for further improvement. We will be finalizing by Monday or Tuesday.  To the vendors who do not get feedback from us, thank you very much for participation. We may still do business in future for some of our other needs. 
The following are the process steps / expectations going forward, 
1. Feedback to the shortlisted designers and inviting improvements.
2. Review of the improved designs and further shortlist & feedback or direct finalization.
3. The design should be in 1024*768
2. Number of page designs = 2 (home page, inner page).
4. Home page design: instead of delivery model and customers, show one link "Why Us".
4. Solutions page design:  We will be needing an image in center column of solutions page that in a nutshell gives all the different types of solutions we provide. The entire set of solutions is in our attached document website for brightvale - template v4 and I am just uploading v5 with more description on sublinks.
5. After selection, we will be needing images for all the solution pages (total 12 pages under solutions + one solutions page), 1 image for Why Us?, 1 for Careers, and 3 for company (about us/ team, core values, ...) = total 18

Rgds
Rajesh Kothuri

Target Market(s)

We are a sales analytics and sales productivity services company. We help B2B companies with: sales planning; sales operations and sales measurement. The characteristics of our customers are:
- B2B medium enterprises (USD 100M- USD 2B in revenue) in the US
- Primary target verticals are: high-tech, engineering and professional services firms
- Our primary target customers titles are VP of Sales or VP of marketing; we could be selling to the CEO at companies with revenues below $200M

Industry/Entity Type

Consulting

Requirements
Must have
• - Clean, uncluttered design
• - Easy navigation; minimum clicks
Nice to have
• We have already built a content management system and wireframes for this site. To the extent possible, it would be great to leverage the wireframe structure we built, provided you don’t have to compromise on the look and feel and navigation of the site. Below is what we currently have as banner sizes and resolutions are:
• Home page banner size: 950 * 250’
• All pages – center top - image size: 558 * 160
• All pages – right hand top image – 175*135’

```html
<!DOCTYPE html>
<html lang="en">
<head>
<meta charset="utf-8">
<title>Brightvale – Solutions</title>
<link href="https://fonts.googleapis.com/css2?family=Open+Sans:wght@400;600;700&family=Arimo:wght@400;700&family=Roboto+Condensed:wght@700&display=swap" rel="stylesheet">
<style>
  :root{
    --blue:#0b6db5;
    --blue-dark:#07589a;
    --link:#0a62b0;
    --green:#4a9a3c;
    --green-dark:#3a7f2e;
    --green-light:#6fba55;
    --text:#222;
    --bg-top:#ffffff;
    --bg-bottom:#9c9c9c;
  }
  *{box-sizing:border-box;margin:0;padding:0}
  html,body{width:1200px;height:798px;overflow:hidden}
  body{
    position:relative;
    font-family:"Arimo",Arial,sans-serif;
    color:var(--text);
    background:linear-gradient(to bottom,var(--bg-top) 0,#fff 330px,#e4e4e4 560px,var(--bg-bottom) 798px);
  }
  a{text-decoration:none;color:inherit}

  /* Utility bar */
  .utility-bar{position:absolute;left:0;top:0;width:1200px;height:42px;background:linear-gradient(to bottom,#0f74bd,var(--blue-dark))}
  .utility-item{position:absolute;top:11px;display:flex;align-items:center;gap:7px;color:#fff;font-family:"Open Sans",sans-serif;font-size:13px;font-weight:600;letter-spacing:-.2px}
  .utility-item .ico{width:19px;height:19px;border-radius:50%;background:#fff;display:flex;align-items:center;justify-content:center}
  .utility-signin{left:54px;top:0;width:160px;height:51px;padding-top:11px;padding-left:8px;align-items:flex-start;background:linear-gradient(to bottom,#5fae48,#3f8d31);border-radius:0 0 5px 5px;border:1px solid #9fd08a;border-top:none}
  .utility-contact{left:227px}
  .utility-sitemap{left:355px}

  /* Brand */
  .brand{position:absolute;left:62px;top:104px;display:flex;align-items:center;gap:9px}
  .brand-mark{width:20px;height:20px;border-radius:50%;background:var(--blue)}
  .brand-name{font-family:"Open Sans",sans-serif;font-size:26px;font-weight:400;letter-spacing:2px;color:var(--blue)}

  /* Main nav */
  .main-nav{position:absolute;right:76px;top:116px;display:flex;align-items:center;font-family:"Open Sans",sans-serif;font-weight:700;font-size:14px;color:var(--blue)}
  .main-nav a{padding:3px 10px}
  .main-nav .sep{color:var(--green);font-weight:400}
  .main-nav .is-active{background:linear-gradient(to bottom,#5fae48,#3a842d);color:#fff;border-radius:12px;border:1px solid #2f6e25;padding:2px 11px}

  /* Page panel */
  .page-panel{position:absolute;left:48px;top:185px;width:1090px;height:565px;background:#fff;border-radius:0 0 12px 12px;box-shadow:0 6px 14px rgba(0,0,0,.12)}

  /* Sidebar */
  .sidebar{position:absolute;left:57px;top:185px;width:215px}
  .side-head{height:38px;display:flex;align-items:center;gap:8px;padding-left:8px;background:linear-gradient(to bottom,#fbfbfb,#dcdcdc);border:1px solid #cfcfcf;border-radius:4px 4px 0 0;font-family:"Roboto Condensed",sans-serif;font-weight:700;font-size:14.5px;color:var(--green-dark);white-space:nowrap}
  .side-head .toggle{width:15px;height:15px;flex:none;background:var(--green);border:1px solid var(--green-dark);display:flex;align-items:center;justify-content:center}
  .side-sub{padding:14px 0 6px 13px;background:linear-gradient(to bottom,#f1f1f1,#fff 40%)}
  .side-sub li{list-style:none;width:192px;height:25px;line-height:22px;border-bottom:1px dotted #bbb;font-family:"Open Sans",sans-serif;font-size:11.5px;color:#222;display:flex;align-items:center;gap:7px}
  .side-sub li.is-current{font-weight:700;font-size:12.5px}
  .side-sub li::before{content:"";width:0;height:0;border-left:4px solid #333;border-top:3px solid transparent;border-bottom:3px solid transparent}
  .side-sub + .side-head{margin-top:4px}
  .side-head + .side-head{margin-top:7px}

  /* Hero */
  .hero{position:absolute;left:284px;top:185px;width:626px;height:181px;background:linear-gradient(100deg,#0a68b6 0%,#2b93d6 45%,#5cc0ea 75%,#1f7fc7 100%)}
  .hero-copy{position:absolute;left:13px;top:96px;color:#fff;font-family:"Open Sans",sans-serif}
  .hero-title{font-size:24px;font-weight:700;letter-spacing:-.4px;line-height:1}
  .hero-sub{margin-top:4px;font-size:15.5px;font-weight:600;line-height:19px;letter-spacing:-.2px}

  /* Side feature */
  .feature{position:absolute;left:926px;top:185px;width:197px}
  .feature-image{height:152px;background:linear-gradient(135deg,#c6cfd6,#8c9aa5 55%,#b9c2c9)}
  .feature-label{height:29px;background:var(--green);color:#fff;font-family:"Roboto Condensed",sans-serif;font-weight:700;font-size:14px;line-height:29px;padding-left:8px}
  .feature-text{margin-top:15px;padding:0 2px 0 12px;font-size:13.3px;line-height:18.5px;text-align:justify;hyphens:auto;-webkit-hyphens:auto;color:#222}
  .feature-text p + p{margin-top:18.5px}
  .feature-rule{position:absolute;left:926px;top:366px;width:1px;height:350px;background:linear-gradient(to bottom,#ddd,#fff)}

  /* Solutions box */
  .solutions{position:absolute;left:286px;top:379px;width:626px;height:323px;border:1px solid #e3e3e3;border-radius:6px;background:#fff}
  .solutions-banner{position:absolute;left:10px;top:12px;width:608px;height:89px;border-radius:6px;background:linear-gradient(to bottom,#d8d8d8,#a8a8a8)}
  .solutions-banner h1{position:absolute;left:12px;bottom:9px;color:#fff;font-family:"Open Sans",sans-serif;font-weight:700;font-size:25px;letter-spacing:-.3px}
  .solution-col{position:absolute;top:118px;width:180px}
  .solution-col h2{font-family:"Roboto Condensed",sans-serif;font-weight:700;font-size:14.5px;line-height:16px;color:var(--green-dark)}
  .solution-col p{margin-top:9px;font-size:13.3px;line-height:16px;color:#111}
  .solution-col ul{margin-top:10px;list-style:none}
  .solution-col li{font-size:13.3px;line-height:16.4px;color:var(--link);display:flex;align-items:center;gap:6px}
  .solution-col li::before{content:"";width:0;height:0;border-left:4px solid var(--green-light);border-top:3px solid transparent;border-bottom:3px solid transparent}
  .col-planning{left:15px}
  .col-operations{left:225px;top:114px}
  .col-measurement{left:437px}
  .col-divider{position:absolute;top:112px;width:1px;height:200px;border-left:1px dotted #cfcfcf}
  .col-divider-1{left:206px}
  .col-divider-2{left:418px}

  /* Footer */
  .footer{position:absolute;top:766px;left:58px;width:1065px;display:flex;justify-content:space-between;color:#fff;font-size:13.5px}
</style>
</head>
<body>

<header>
  <nav class="utility-bar" aria-label="Account">
    <a class="utility-item utility-signin" href="#">
      <span class="ico"><svg width="11" height="11" viewBox="0 0 11 11"><path d="M1 5.5h6M5 3l2.5 2.5L5 8M7.5 1.5h2v8h-2" fill="none" stroke="#3f8d31" stroke-width="1.5"/></svg></span>SIGN IN / REGISTER</a>
    <a class="utility-item utility-contact" href="#">
      <span class="ico"><svg width="11" height="11" viewBox="0 0 11 11"><rect x="3.5" y="1" width="4" height="3" fill="none" stroke="#0b6db5"/><rect x="0.5" y="7" width="4" height="3" fill="none" stroke="#0b6db5"/><rect x="6.5" y="7" width="4" height="3" fill="none" stroke="#0b6db5"/><path d="M5.5 4v1.5M2.5 7V5.5h6V7" fill="none" stroke="#0b6db5"/></svg></span>CONTACT &nbsp;US</a>
    <a class="utility-item utility-sitemap" href="#">
      <span class="ico"><svg width="11" height="9" viewBox="0 0 11 9"><rect x="0.5" y="0.5" width="10" height="8" fill="none" stroke="#3f8d31"/><path d="M0.5 0.5l5 4 5-4" fill="none" stroke="#3f8d31"/></svg></span>SITEMAP</a>
  </nav>

  <a class="brand" href="#"><span class="brand-mark"></span><span class="brand-name">BRIGHTVALE</span></a>

  <nav class="main-nav" aria-label="Main">
    <a href="#">Home</a>
    <a class="is-active" href="#">Solutions</a>
    <a href="#">Why Us</a><span class="sep">|</span>
    <a href="#">Company</a><span class="sep">|</span>
    <a href="#">Careers</a>
  </nav>
</header>

<div class="page-panel"></div>

<aside class="sidebar">
  <div class="side-head"><span class="toggle"><svg width="7" height="5" viewBox="0 0 7 5"><path d="M0 0h7L3.5 5z" fill="#fff"/></svg></span>Sales Planning Analytics</div>
  <ul class="side-sub">
    <li>Customer Targeting</li>
    <li>Territory Planning</li>
    <li class="is-current">Campaign Planning</li>
  </ul>
  <div class="side-head"><span class="toggle"><svg width="5" height="7" viewBox="0 0 5 7"><path d="M0 0v7l5-3.5z" fill="#fff"/></svg></span>Sales Productivity Centers</div>
  <div class="side-head"><span class="toggle"><svg width="5" height="7" viewBox="0 0 5 7"><path d="M0 0v7l5-3.5z" fill="#fff"/></svg></span>Sales Measurement Analytics</div>
</aside>

<section class="hero" role="img" aria-label="Two business people shaking hands in front of a rising stock chart">
  <div class="hero-copy">
    <div class="hero-title">Do more with less.</div>
    <div class="hero-sub">No upfront software, hardware,<br>people or training costs for you. Pay as you go.</div>
  </div>
</section>

<aside class="feature">
  <div class="feature-image" role="img" aria-label="Colleagues reviewing printed reports at a desk"></div>
  <div class="feature-label">Sales Operations Support</div>
  <div class="feature-text">
    <p>Vestibulum lectus arcu, iaculis non iaculis ultrices, ultricies sit amet nisi. Nullam dictum nunc et metus dapibus scelerisque. Etiam quis sapien in purus consequat ornare.</p>
    <p>Praesent vitae ipsum lorem. Nullam ac orci mi, sed pellen&shy;tesque dolor. Nullam dictum nunc et metus dapibus scelerisque. Etiam quis sapien in purus consequat ornare. Praesent vitae ipsum lorem. Nullam ac orci mi, sed pellen&shy;tesque dolor.</p>
  </div>
</aside>
<div class="feature-rule"></div>

<main class="solutions">
  <div class="solutions-banner" role="img" aria-label="Grey silhouettes of a business team in front of a world map"><h1>Solutions</h1></div>

  <div class="solution-col col-planning">
    <h2>Sales Planning<br>Analytics</h2>
    <p>We help target the right customers, allocate resources effectively and increase return on sales &amp; marketing $.</p>
    <ul><li>Customer Targeting</li><li>Territory Planning</li><li>Campaign Planning</li></ul>
  </div>
  <div class="col-divider col-divider-1"></div>
  <div class="solution-col col-operations">
    <h2>Sales Operations<br>Support</h2>
    <p>This is all about saving time for sales reps and improving their productivity.</p>
    <ul><li>Quoting center</li><li>Proposal center</li><li>CRM center</li><li>Partner center</li><li>Reference center</li><li>Deal center</li></ul>
  </div>
  <div class="col-divider col-divider-2"></div>
  <div class="solution-col col-measurement">
    <h2>Sales Measurement<br>Analytics</h2>
    <p>This is all about improving sales efficiency by providing actionable insights.</p>
    <ul><li>Business Reporting</li><li>Metrics &amp; Benchmarking</li><li>Pipeline health check</li><li>Sales rep scorecards</li><li>What-if analyses</li><li>Data services.</li></ul>
  </div>
</main>

<footer class="footer">
  <span>Contact Us | Sitemap &nbsp;| &nbsp;Disclaimer</span>
  <span>© 2010. Brightvale, Inc. All Rights Reserved</span>
</footer>

</body>
</html>
```